Business card por a urban DJ, up scale audience target

Need a sober design, modern, conservative colors but i can consider some options, y play rnb, hip hop, EDM and top40.

Business card for contact and personal info, double sided, use logo attrached please; im 42 so i need a card acording to my age an target audience.

Target Market(s)

Adult people, up scale audience

Industry/Entity Type

Music Download

Contact Information for Business Card

Cel (318) 4207265518 www.lumadrift.com

Requirements
Must have
• open mind
Nice to have
• open mind
Should not have
• DJ

```html
<!DOCTYPE html>
<html lang="en">
<head>
<meta charset="UTF-8">
<title>Lumadrift Business Card</title>
<link rel="stylesheet" href="https://fonts.googleapis.com/css2?family=Jost:wght@400;500;600;700&display=swap">
<style>
  :root {
    --stage: #3b3e42;
    --card-dark: #151515;
    --card-light: #f6f6f6;
    --ink-light: #f2f2f2;
    --ink-dark: #111111;
  }
  * { margin: 0; padding: 0; box-sizing: border-box; }
  html, body {
    width: 1200px;
    height: 750px;
    overflow: hidden;
  }
  body {
    background: var(--stage);
    font-family: "Jost", "Futura", sans-serif;
    position: relative;
  }
  .card {
    position: absolute;
    top: 229px;
    width: 462px;
    height: 262px;
  }
  .card--front {
    left: 124px;
    background: var(--card-dark);
    color: var(--ink-light);
    text-align: center;
  }
  .card--back {
    left: 618px;
    background: var(--card-light);
    display: flex;
    align-items: center;
    justify-content: center;
  }
  .contact {
    position: absolute;
    left: 0;
    right: 0;
    top: 82px;
  }
  .contact__name {
    font-size: 23px;
    font-weight: 500;
    letter-spacing: 0.2px;
    line-height: 1;
  }
  .contact__role {
    margin-top: 8px;
    font-size: 16px;
    font-weight: 500;
    line-height: 1;
  }
  .contact__rule {
    width: 183px;
    margin: 10px auto 0;
    border-top: 1px dotted var(--ink-light);
  }
  .contact__phone {
    margin-top: 9px;
    font-size: 16px;
    font-weight: 400;
    line-height: 1;
  }
  .contact__web {
    margin-top: 7px;
    font-size: 15px;
    font-weight: 400;
    line-height: 1;
  }
  .brand {
    display: flex;
    align-items: flex-start;
    gap: 8px;
  }
  .brand__name {
    font-size: 64px;
    font-weight: 700;
    color: var(--ink-dark);
    letter-spacing: 2px;
    line-height: 1;
  }
  .brand__mark {
    width: 18px;
    height: 18px;
    background: var(--ink-dark);
    margin-top: 4px;
  }
</style>
</head>
<body>
  <section class="card card--front">
    <div class="contact">
      <p class="contact__name">MARCUS HALE</p>
      <p class="contact__role">CEO/FOUNDER</p>
      <div class="contact__rule"></div>
      <p class="contact__phone">(318) 4207265518</p>
      <p class="contact__web">www.lumadrift.com</p>
    </div>
  </section>
  <section class="card card--back">
    <div class="brand">
      <span class="brand__name">LUMA</span>
      <span class="brand__mark"></span>
    </div>
  </section>
</body>
</html>
```